Renny Oskow - Free Personalised Health Consultation - "One size does not fit all"

This flyer will be left on tables/seats at speaking events and seminars and used to attain leads.

Top half will have "SMS me for a FREE Personalised Health Consultation" and my picture (see www.rennyoskow-demo.com and pick most engaging photo) and underneath my contact details. It must have lines with "Notes:" halfway down so people can take notes at the seminar and lines on the back with my contact details again and "Notes: with lines.

I am having a business card also being designed by Artvane for same and would like the flyer and business card to carry a similar feel/look for consistency.

Below is the brief for the business card being designed:
Business Card for www.rennyoskow-demo.com site. It is a trust site and I use it for 1:1 relatable connections. It is the one I use for building intimate 1:1 trust building and Exec Coaching Services and programs for high wealth individuals and corporates. I also have a commercial programmatic site of my personal health products and services and programs for main stream one to many. www.steadyforwardliving-demo.com that can also provoke thought for the www.rennyoskow-demo.com business card. (mind you will get a separate business card for that site, but want to provide context). It has a logo which you may want to draw from in designing the rennyoskow business card which is personal and is about building my brand. There is also a rennyoskow personal PX page and rennyoskow business PX page. I am a Certified Talent Compass 3.1 Coach with Norvik and you can get a corporate brief of me on there to give you more context https://www.norvikcoachhub-demo.com/coach/en-us/directory?search=renny

Target Market(s)

Exec, IT, Health conscious. Corporates wanting to run Health and Wellness programs. Those wanting to go from good to great. Millennials to Middleaged.

Industry/Entity Type

Health And Wellness

Font styles to use
Sans Serif
Other font styles liked:
• Arial and Calibri ok too

Colors

Designer to choose colors to be used in the design.

Requirements
Must have
• Picture of me - use best from www.rennyoskow-demo.com or can send one you choose.
• Contact details like my buisness card being designed by you guys in separate project.
• Name: Renny Oskow
• email: renny@rennyoskow-demo.,com
• Phone: Australia +61 400 000 137 Singapore: +65 9000 2468
Nice to have
• Open to ideas

```html
<!DOCTYPE html>
<html lang="en">
<head>
<meta charset="utf-8">
<title>Renny Oskow – Seminar Notes Flyer</title>
<link href="https://fonts.googleapis.com/css2?family=Oswald:wght@300;400;500;600&family=Open+Sans:wght@400;600&family=Tinos:wght@700&display=swap" rel="stylesheet">
<style>
  :root {
    --canvas: #e9e9e9;
    --paper: #ffffff;
    --panel: #333333;
    --ink: #1f1f1f;
    --rule: #9a9a9a;
    --photo-light: #e4e4e4;
    --photo-dark: #8a8a8a;
    --ghost: #f1f1f1;
  }
  * { box-sizing: border-box; margin: 0; padding: 0; }
  html, body { width: 1200px; height: 1200px; overflow: hidden; }
  body {
    background: var(--canvas);
    font-family: "Open Sans", Arial, sans-serif;
    color: var(--ink);
    position: relative;
  }
  .flyer {
    position: absolute;
    top: 230px;
    width: 540px;
    height: 720px;
    background: var(--paper);
    box-shadow: 0 2px 8px rgba(0,0,0,.12);
    overflow: hidden;
  }
  .flyer--front { left: 40px; }
  .flyer--back { left: 620px; }

  /* Front hero */
  .hero { position: absolute; left: 0; top: 0; width: 540px; height: 440px; display: flex; }
  .hero__photo {
    width: 250px; height: 100%;
    background: linear-gradient(160deg, var(--photo-light) 0%, #c8c8c8 45%, var(--photo-dark) 100%);
  }
  .hero__panel {
    flex: 1; background: var(--panel); color: #fff;
    display: flex; flex-direction: column; align-items: center;
    padding-top: 74px; position: relative;
  }
  .offer__lead { font-family: "Oswald", sans-serif; font-weight: 300; font-size: 42px; line-height: 1; }
  .offer__free { font-family: "Oswald", sans-serif; font-weight: 500; font-size: 124px; line-height: 1; letter-spacing: 1px; margin-top: 2px; }
  .offer__kind { font-family: "Oswald", sans-serif; font-weight: 400; font-size: 44px; line-height: 1; margin-top: 4px; }
  .offer__service {
    font-family: "Oswald", sans-serif; font-weight: 600; font-size: 26px; line-height: 1;
    background: #fff; color: var(--ink); padding: 6px 8px 7px; margin-top: 10px;
  }
  .signature {
    position: absolute; right: 26px; bottom: 40px;
    font-family: "Tinos", serif; font-weight: 700; font-size: 21px;
  }

  /* Notes */
  .notes__label { position: absolute; font-size: 13px; font-weight: 600; letter-spacing: .3px; }
  .notes__line { position: absolute; height: 1px; background: var(--rule); }

  /* Contact bar */
  .contact-bar {
    position: absolute; left: 0; width: 540px; height: 26px;
    background: var(--panel); color: #fff;
    display: flex; align-items: center; justify-content: space-between;
    padding: 0 18px; font-size: 11px; font-weight: 600;
  }
  .contact-bar__item { display: flex; align-items: center; gap: 4px; white-space: nowrap; }
  .contact-bar__item svg { width: 10px; height: 10px; fill: #fff; }

  /* Back */
  .ghost-portrait {
    position: absolute; left: 80px; top: 40px; width: 380px; height: 600px;
    background: radial-gradient(ellipse at 50% 40%, var(--ghost) 0%, #f7f7f7 55%, var(--paper) 80%);
  }
</style>
</head>
<body>

<section class="flyer flyer--front">
  <div class="hero">
    <div class="hero__photo" role="img" aria-label="Black and white portrait of Renny Oskow, arms folded, hand at chin"></div>
    <div class="hero__panel">
      <p class="offer__lead">SMS me for a</p>
      <p class="offer__free">FREE</p>
      <p class="offer__kind">Personalised</p>
      <p class="offer__service">Health Consultation</p>
      <p class="signature">– Renny Oskow</p>
    </div>
  </div>

  <p class="notes__label" style="left:30px; top:464px;">NOTES</p>
  <div class="notes__line" style="left:30px; right:30px; top:496px;"></div>
  <div class="notes__line" style="left:30px; right:30px; top:528px;"></div>
  <div class="notes__line" style="left:30px; right:30px; top:560px;"></div>
  <div class="notes__line" style="left:30px; right:30px; top:592px;"></div>
  <div class="notes__line" style="left:30px; right:30px; top:624px;"></div>

  <div class="contact-bar" style="top:658px;">
    <span class="contact-bar__item"><svg viewBox="0 0 10 10"><path d="M2 0.5l2 2-1 1.2c.6 1.3 1.5 2.2 2.8 2.8L7 5.5l2 2-1.3 1.8C4 9 1 6 .7 1.8z"/></svg>Australia +61 400 000 137</span>
    <span class="contact-bar__item"><svg viewBox="0 0 10 10"><path d="M2 0.5l2 2-1 1.2c.6 1.3 1.5 2.2 2.8 2.8L7 5.5l2 2-1.3 1.8C4 9 1 6 .7 1.8z"/></svg>Singapore: +65 9000 2468</span>
    <span class="contact-bar__item"><svg viewBox="0 0 10 10"><path d="M0 2h10v6H0z M0 2l5 3.5L10 2" fill="none" stroke="#fff" stroke-width="1"/></svg>renny@rennyoskow-demo.,com</span>
  </div>
</section>

<section class="flyer flyer--back">
  <div class="ghost-portrait" role="img" aria-label="Faint background portrait of Renny Oskow, arms folded"></div>
  <p class="notes__label" style="left:30px; top:26px;">NOTES</p>
  <div class="notes__line" style="left:30px; right:30px; top:66px;"></div>
  <div class="notes__line" style="left:30px; right:30px; top:96px;"></div>
  <div class="notes__line" style="left:30px; right:30px; top:126px;"></div>
  <div class="notes__line" style="left:30px; right:30px; top:156px;"></div>
  <div class="notes__line" style="left:30px; right:30px; top:186px;"></div>
  <div class="notes__line" style="left:30px; right:30px; top:216px;"></div>
  <div class="notes__line" style="left:30px; right:30px; top:246px;"></div>
  <div class="notes__line" style="left:30px; right:30px; top:276px;"></div>
  <div class="notes__line" style="left:30px; right:30px; top:306px;"></div>
  <div class="notes__line" style="left:30px; right:30px; top:336px;"></div>
  <div class="notes__line" style="left:30px; right:30px; top:366px;"></div>
  <div class="notes__line" style="left:30px; right:30px; top:396px;"></div>
  <div class="notes__line" style="left:30px; right:30px; top:426px;"></div>
  <div class="notes__line" style="left:30px; right:30px; top:456px;"></div>
  <div class="notes__line" style="left:30px; right:30px; top:486px;"></div>
  <div class="notes__line" style="left:30px; right:30px; top:516px;"></div>
  <div class="notes__line" style="left:30px; right:30px; top:546px;"></div>
  <div class="notes__line" style="left:30px; right:30px; top:576px;"></div>
  <div class="notes__line" style="left:30px; right:30px; top:606px;"></div>
  <div class="notes__line" style="left:30px; right:30px; top:636px;"></div>

  <div class="contact-bar" style="top:670px;">
    <span class="contact-bar__item"><svg viewBox="0 0 10 10"><path d="M2 0.5l2 2-1 1.2c.6 1.3 1.5 2.2 2.8 2.8L7 5.5l2 2-1.3 1.8C4 9 1 6 .7 1.8z"/></svg>Australia +61 400 000 137</span>
    <span class="contact-bar__item"><svg viewBox="0 0 10 10"><path d="M2 0.5l2 2-1 1.2c.6 1.3 1.5 2.2 2.8 2.8L7 5.5l2 2-1.3 1.8C4 9 1 6 .7 1.8z"/></svg>Singapore: +65 9000 2468</span>
    <span class="contact-bar__item"><svg viewBox="0 0 10 10"><path d="M0 2h10v6H0z M0 2l5 3.5L10 2" fill="none" stroke="#fff" stroke-width="1"/></svg>renny@rennyoskow-demo.,com</span>
  </div>
</section>

</body>
</html>
```